Varsity Purse Wordpress Website (re)design

we are a student run financial literacy website and are desperately trying to get college students to pay attention to the finances to create solid financial skills for life. This age group LOVES pixolette so instead of sharing a lot of text we want to tease through graphics/infographics topics that are relevant to them based on what their peers are discussing and then push them to our resources to learn more. ultimately we will also recommend products to them that are carefully selected by us. these will range from a book on paying back their student loan to a place to store their dorm stuff when they go home for summer break to a credit card we determine is best for them. So yes, commerce is imp but SEO to attract students comes first which we will do through survey monkey and cash prizes. we need to capture email address. we also have a "checklist" (attached and needs rebranding) of the basic and most imp money matters for them. Each item will hyperlink to our parnter, nuvoe, and need to do so seamlessly and push them back to us.

Target Market(s)

college students and young adults

Requirements
Must have
• simple, clean and graphic with an integration of survey monkey, an borvel store and a capture of emails through mailchimp or other similar. Ability to edit after ourselves on wordpress

```html
<!DOCTYPE html>
<html lang="en">
<head>
<meta charset="utf-8">
<title>Varsity Purse – Take Charge of your Change</title>
<link href="https://fonts.googleapis.com/css2?family=Lato:ital,wght@0,400;0,700;0,900;1,400&display=swap" rel="stylesheet">
<style>
:root{
  --blue:#1d5fa3;
  --navy:#1a3d6e;
  --green:#55b03b;
  --green-dark:#3f9a2c;
  --text:#333333;
  --muted:#555555;
  --grey-band:#efefef;
  --teal:#1f6c86;
  --footer:#2b2b2b;
  --white:#ffffff;
}
*{box-sizing:border-box;margin:0;padding:0}
html,body{width:1200px;height:3323px;overflow:hidden;background:var(--white)}
body{position:relative;font-family:'Lato',sans-serif;color:var(--text)}
.abs{position:absolute}

/* header */
.site-header{left:0;top:0;width:1200px;height:105px;background:var(--white)}
.brand{display:flex;align-items:center;gap:10px;font-weight:700;color:var(--blue);font-family:'Lato',sans-serif}
.brand-dot{border-radius:50%;background:var(--green)}
.header-brand{left:75px;top:34px;font-size:30px}
.header-brand .brand-dot{width:24px;height:24px}
.main-nav{left:302px;top:52px;display:flex;gap:0}
.main-nav a{font-size:13px;font-weight:700;color:#333;text-decoration:none;text-transform:uppercase;margin-right:45px;letter-spacing:.2px}
.main-nav a.active{color:var(--blue)}
.login-btn{left:992px;top:41px;width:134px;height:39px;border:1.5px solid var(--blue);color:var(--blue);font-size:14px;font-weight:700;display:flex;align-items:center;justify-content:center}

/* hero */
.hero{left:0;top:105px;width:1200px;height:700px}
.hero-photo{position:absolute;inset:0;background:linear-gradient(160deg,#b9cbe0 0%,#7d97b8 35%,#4a5d78 60%,#2d3340 100%)}
.hero-wave{position:absolute;left:0;top:0}
.hero-card{left:75px;top:277px;width:347px;height:230px;background:rgba(255,255,255,.92);text-align:center;padding-top:26px}
.hero-card h1{font-size:38px;font-weight:900;color:#2a2a2a;letter-spacing:.5px}
.hero-card p{font-size:24px;color:#333;line-height:30px;margin-top:4px}
.btn-green{background:var(--green);color:var(--white);font-size:15px;font-weight:700;text-transform:uppercase;display:flex;align-items:center;justify-content:center}
.hero-card .btn-green{width:291px;height:50px;margin:18px auto 0}

/* welcome */
.welcome-brand{left:75px;top:870px;font-size:60px}
.welcome-brand .brand-dot{width:40px;height:40px}
.section-title{font-size:34px;font-weight:700;text-transform:uppercase;letter-spacing:.3px}
.welcome-title{left:432px;top:813px;color:var(--blue)}
.welcome-text{left:432px;top:872px;width:670px;font-size:17px;line-height:28px;color:#333}
.welcome-btn{left:432px;top:984px;width:169px;height:48px}

/* features */
.band{left:0;top:1058px}
.feature{top:1196px;width:331px;height:371px;background:var(--white);text-align:center;padding:30px 28px 0}
.feature-icon{width:102px;height:102px;border-radius:50%;background:var(--green);margin:0 auto;display:flex;align-items:center;justify-content:center}
.feature h3{color:var(--green);font-size:19px;font-weight:700;text-transform:uppercase;line-height:28px;margin-top:28px}
.feature p{font-size:15px;line-height:26px;color:#444;margin-top:4px}
.btn-outline{border:1.5px solid #555;color:var(--blue);font-size:15px;font-weight:700;width:151px;height:42px;display:flex;align-items:center;justify-content:center;margin:14px auto 0}

/* why */
.why-title{left:75px;top:1746px;color:#333;line-height:38px}
.why-photo{left:75px;top:1851px;width:601px;height:198px;background:linear-gradient(90deg,#3e5a2a 0%,#86905a 45%,#c7b48a 70%,#6c7a4a 100%)}
.why-text{left:75px;top:2071px;width:610px;font-size:16.5px;line-height:28px;color:#333}
.why-btn{left:75px;top:2233px;width:169px;height:48px}
.check-title{left:739px;top:1746px;color:#333}
.checklist{left:739px;top:1819px;width:341px;height:464px;background:linear-gradient(180deg,#e9eef8 0 35px,#8ec0ec 35px,#7fb5e6 100%);border:1px solid #c9d7ea}
.divider{left:75px;top:2365px;width:1051px;height:1px;background:#d9d9d9}

/* testimonials */
.quotes-title{left:0;top:2420px;width:1200px;text-align:center;color:#333;font-size:33px}
.green-bg{left:0;top:2500px}
.quote{top:2510px;width:331px;height:248px;background:var(--white);text-align:center;padding:22px 26px 0;border:1px solid #e3e3e3}
.avatar{width:68px;height:68px;border-radius:50%;background:linear-gradient(180deg,#c9cfd6,#8b96a3);margin:0 auto}
.quote p{font-style:italic;font-size:14px;line-height:24px;color:#333;margin-top:14px}
.quote cite{display:block;font-style:normal;font-weight:700;color:var(--blue);font-size:13px;margin-top:8px}

/* contact */
.contact-title{color:var(--white);top:2826px}
.field{background:var(--white);font-size:13.5px;color:#222;padding:12px 12px;height:40px}
.submit{left:75px;top:3145px;width:178px;height:48px;background:#111;color:var(--white);font-size:14px;font-weight:700;display:flex;align-items:center;justify-content:center}
.info-line{left:614px;color:var(--white);font-size:19px;display:flex;align-items:center;gap:16px}
.map{left:614px;top:2971px;width:512px;height:222px;background:linear-gradient(90deg,#dfe6dc 0%,#d6dfd0 55%,#a9cdea 68%,#9fc7e8 100%)}

/* footer */
.site-footer{left:0;top:3240px;width:1200px;height:83px;background:var(--footer);color:#ddd}
.copyright{left:75px;top:33px;font-size:12.5px}
.social{right:60px;top:31px;display:flex;gap:18px;font-size:13px;font-weight:700;color:var(--white)}
</style>
</head>
<body>

<header class="site-header abs">
  <div class="brand header-brand abs"><span>Varsity Purse</span><span class="brand-dot"></span></div>
  <nav class="main-nav abs">
    <a class="active">Home</a><a>Take the Pledge</a><a>Blog</a><a>About Us</a><a>Tips &amp; Tricks</a><a>About nuvoe</a>
  </nav>
  <div class="login-btn abs">LOG IN</div>
</header>

<section class="hero abs">
  <div class="hero-photo" role="img" aria-label="Graduate in cap and gown holding a piggy bank in front of a campus building"></div>
  <svg class="hero-wave" width="1200" height="700" viewBox="0 0 1200 700" aria-hidden="true">
    <path d="M0 700 L0 675 C120 610 250 590 380 610 C520 632 640 665 760 640 C900 612 1050 560 1200 525 L1200 700 Z" fill="#ffffff"/>
    <path d="M0 690 C120 600 250 580 380 600 C520 622 640 655 760 630 C900 602 1050 550 1200 515 L1200 528 C1050 563 900 617 760 645 C640 670 520 640 380 618 C250 598 120 618 0 700 Z" fill="#55b03b"/>
  </svg>
  <div class="hero-card abs" style="left:75px;top:172px">
    <h1>VARSITY PURSE</h1>
    <p>Take Charge of your<br>Change</p>
    <div class="btn-green">Read More</div>
  </div>
</section>

<div class="brand welcome-brand abs"><span>Varsity Purse</span><span class="brand-dot"></span></div>
<h2 class="section-title welcome-title abs">Welcome to our website</h2>
<p class="welcome-text abs">Welcome to your FREE resource that will help you achieve financial independence and knowledge.Using peer-to-peer tips, personal stories and nuvoe, you can become a Varsity Purse!</p>
<div class="btn-green welcome-btn abs">Read More</div>

<svg class="band abs" width="1200" height="640" viewBox="0 0 1200 640" aria-hidden="true">
  <path d="M0 50 C150 90 300 20 450 40 C600 60 700 110 850 90 C1000 70 1100 10 1200 0 L1200 560 C1080 520 950 470 800 500 C640 535 520 600 360 590 C220 580 110 610 0 632 Z" fill="var(--grey-band)"/>
</svg>

<article class="feature abs" style="left:75px">
  <div class="feature-icon"><svg width="44" height="52" viewBox="0 0 44 52"><path d="M2 2h28l12 12v36H2z" fill="#fff"/><path d="M10 24h24M10 32h24M10 40h24" stroke="#55b03b" stroke-width="3"/></svg></div>
  <h3>How to Budget</h3>
  <p>Having a solid budget is a fundamental building block in becoming financially independent, so here is a breakdown of the purpose behind...</p>
  <div class="btn-outline">READ MORE</div>
</article>
<article class="feature abs" style="left:435px">
  <div class="feature-icon"><svg width="54" height="34" viewBox="0 0 54 34"><rect x="2" y="2" width="50" height="30" rx="3" fill="none" stroke="#fff" stroke-width="4"/><circle cx="27" cy="17" r="8" fill="#fff"/><rect x="9" y="9" width="5" height="16" fill="#fff"/><rect x="40" y="9" width="5" height="16" fill="#fff"/></svg></div>
  <h3>Money Saving Hacks for Millennials</h3>
  <p>The other generations love to pick on us, but the unemployment rate is the lowest it's been in over 50 years..</p>
  <div class="btn-outline">READ MORE</div>
</article>
<article class="feature abs" style="left:795px">
  <div class="feature-icon"><svg width="56" height="40" viewBox="0 0 56 40"><rect x="8" y="2" width="40" height="28" rx="2" fill="none" stroke="#fff" stroke-width="4"/><rect x="2" y="32" width="52" height="5" rx="2" fill="#fff"/></svg></div>
  <h3>How to Create Your Own Side Hustle</h3>
  <p>So, you're thinking of starting a side hustle, but before you do you should think about a few things...</p>
  <div class="btn-outline">READ MORE</div>
</article>

<h2 class="section-title why-title abs">Why take a personal<br>finance course?</h2>
<div class="why-photo abs" role="img" aria-label="Graduation cap and a glass jar of coins resting on an open hand"></div>
<p class="why-text abs">Varsity Purse will teach you how to use your student loan to get a new car, how to fill out those first day of work tax forms without calling mom and dad, and how to build credit without getting into credit card debt.<br>Personal financial skills will keep your wallet full and your options open.<br>Take charge of your finances today!</p>
<div class="btn-green why-btn abs">Read More</div>

<h2 class="section-title check-title abs">Checklist</h2>
<div class="checklist abs" role="img" aria-label="Hearth &amp; Home and Varsity Purse money checklist infographic covering banking, taxes, aid, budgeting, saving and credit"></div>

<div class="divider abs"></div>

<h2 class="section-title quotes-title abs">Don't take our word for it...</h2>

<svg class="green-bg abs" width="1200" height="740" viewBox="0 0 1200 740" aria-hidden="true">
  <defs><linearGradient id="contactGrad" x1="0" y1="1" x2="1" y2="0"><stop offset="0" stop-color="#1f6c86"/><stop offset=".5" stop-color="#2e9170"/><stop offset="1" stop-color="#5cb33a"/></linearGradient></defs>
  <path d="M0 110 C200 170 450 230 700 240 C900 248 1080 190 1200 150 L1200 740 L0 740 Z" fill="url(#contactGrad)"/>
</svg>

<blockquote class="quote abs" style="left:75px">
  <div class="avatar" role="img" aria-label="Portrait of Declan Hartwell"></div>
  <p>“ Believe it or not, I was fifty before I under-stood the difference between gross and net profit. Where was Varsity Purse when I needed it?</p>
  <cite>Declan Hartwell, Founder of Meridian Holdings</cite>
</blockquote>
<blockquote class="quote abs" style="left:435px">
  <div class="avatar" role="img" aria-label="Portrait of Renata Solberg"></div>
  <p>“In today's extra competitive job market, college students need a leg up. Financial literacy skills, like those taught at Varsity Purse, are the answer...”</p>
  <cite>Renata Solberg, Personal Finance Expert</cite>
</blockquote>
<blockquote class="quote abs" style="left:797px">
  <div class="avatar" role="img" aria-label="Portrait of Tobias Keane"></div>
  <p>“ Having personally practiced in the area of personal financial planning for over thirty years, I am thrilled that there is finally a tool that my kids can use to learn...”</p>
  <cite>Tobias Keane, Parent</cite>
</blockquote>

<h2 class="section-title contact-title abs" style="left:75px">Contact Us</h2>
<div class="field abs" style="left:75px;top:2891px;width:247px">Enter Name</div>
<div class="field abs" style="left:338px;top:2891px;width:249px">Email Address</div>
<div class="field abs" style="left:75px;top:2944px;width:247px">Phone No</div>
<div class="field abs" style="left:338px;top:2944px;width:249px">Subject</div>
<div class="field abs" style="left:75px;top:2998px;width:512px;height:131px">Message</div>
<div class="submit abs">SUBMIT</div>

<h2 class="section-title contact-title abs" style="left:614px">Contact Info</h2>
<div class="info-line abs" style="top:2890px"><svg width="14" height="20" viewBox="0 0 14 20"><path d="M7 0a7 7 0 0 1 7 7c0 5-7 13-7 13S0 12 0 7a7 7 0 0 1 7-7z" fill="#fff"/><circle cx="7" cy="7" r="2.6" fill="#2e9170"/></svg>4810 Larkspur Avenue, Suite 210 Brookhaven, FL 32099</div>
<div class="info-line abs" style="top:2922px"><svg width="16" height="16" viewBox="0 0 16 16"><path d="M3 0l3 4-2 2c1 2 4 5 6 6l2-2 4 3-2 3C7 16 0 9 0 3z" fill="#fff"/></svg>1-800-555-0147</div>
<div class="map abs" role="img" aria-label="Street map of the office location near the river"></div>

<footer class="site-footer abs">
  <div class="copyright abs">Copyright © 2019 Company Name . All Right Reserved</div>
  <div class="social abs"><span>Facade</span><span>Chirpa</span><span>Vidora</span><span>Linkwell</span><span>pixolette</span></div>
</footer>

</body>
</html>
```